2-Page Flyer for the Information Session about the Quiet Pathfinder Course

This is a flyer to announce/advertise an evening Information Session about the Quiet Pathfinder Course. This Program aims at mindfully rethinking and redesigning work (and life) for people who feel stuck or not entirely satisfied with their work and/or life (please see draft flyer attached for more details). This Program is property of Bright Meadow, a company that uses a combination of Mindfulness, Design, and Entrepreneurship to help people achieve greater happiness (in their work and lives).

Target Market(s)

People who feel stuck or not entirely satisfied with their work and/or life (please see draft flyer attached for more details)

Font styles to use
Serif
Sans Serif

Colors
ffffff
f37122
33a6d7
acd037

Requirements
Must have
• All of what I will say below is suggestive (I’m not a design expert), and I’m open to divert from it, if it makes sense and feels more interesting.
• I thought initially of a 2-page flyer (please see draft flyer attached). The first page could help people grasp the essence of the event quickly (in 1 or 2 minutes), and then, if they are interested/motivated, they would continue reading through page 2, which has more info about the Program in itself.
• Potential Structure
• Page 1
• . About the Information Session on the Quiet Pathfinder Course
• . Visible Date & Time, Contacts, Venue (and other relevant info)
• . About me (the facilitator)
• Page 2
• . About the Quiet Pathfinder Course
• I include a Powerpoint draft of the flyer with the content. The design is rudimentary and precarious from an aesthetics/organization point of view, and this is mainly where I need help (and maybe in other aspects too!).
• On the flyer, I would like to include:
• . A photo of myself (I attach 1 picture).
• . 1 or 2 beautiful-nature photos (cropped or full). One may have to do with looking at the sky, dreaming, and imagining a new work and life (2 photos with sky and clouds attached). The other has to do with walking the transformation journey (the photo with the person walking through the forest path).
• . bright meadow logo or logos (there are two slightly different ones, that can be used for different purposes). For the first page, I would like the bright meadow logo that has "bright meadow" written on the bottom, with the saying "Stillness, Craft and Venture for Bright Meadow" beneath. This is the main logo. For the 2nd page, you can choose the logo that adapts better.
• - Where it says the "the way out is in" it would be great to have a similar font to the one I attach (see file "Font_the_way_out_is_in.png" and Ankecallig-fg.ttf
Nice to have
• In terms of colours, I would not divert much from the logo colours (and of course white and black). I would like the flyer to be quite white. Almost like fairy-tale white: the white horse, the white snow, the white of the stars, the white heaven. White could be the base colour. White means peace, tranquillity, calm contentment, a smile.
• And then use the other colours. The green of the mindfulness. The blue of the sky, the dreams. And the orange of the sun, the energy, the fire, the action. And maybe the black for text.
• Where it says the "the way out is in" it would be great to have a similar font to the one I attach (see file "Font_the_way_out_is_in".
• I would like this flyer to be a piece of art, in every possible way. Simple, beautiful, ease, light, peaceful, calm happy. Just like the Quiet Pathfinder Course and bright meadow Company that I am creating intends to be. The mission of this Program and Company is to be a designer, a painter (a Picasso) of happier and more fulfilling human lives.
• I am very much looking forward to seeing your proposal(s).

```html
<!DOCTYPE html>
<html lang="en">
<head>
<meta charset="utf-8">
<title>Quiet Pathfinder Course – Information Session Flyer</title>
<link rel="stylesheet" href="https://fonts.googleapis.com/css2?family=Oswald:wght@400;500;600&family=Montserrat:wght@700;800&family=Cabin:ital,wght@0,400;0,600;0,700;1,400;1,600&family=Dancing+Script:wght@600&display=swap">
<style>
  :root{
    --blue:#33a6d7;
    --blue-deep:#2a8ccc;
    --orange:#f37122;
    --green:#acd037;
    --green-deep:#6f9a2e;
    --white:#ffffff;
    --ink:#1f1f1f;
    --ink-soft:#3a3a3a;
    --mist:#eef2f5;
    --paper-grey:#ebebeb;
    --stage:#dfe3e6;
    --black:#111111;
  }
  *{box-sizing:border-box;margin:0;padding:0}
  html,body{width:1200px;height:878px;overflow:hidden}
  body{background:var(--stage);position:relative;font-family:"Cabin",sans-serif;color:var(--ink)}
  .page{position:absolute;top:77px;width:512px;height:724px;background:var(--white);overflow:hidden;box-shadow:0 2px 10px rgba(0,0,0,.18)}
  .page--front{left:77px}
  .page--back{left:610px}
  .abs{position:absolute}

  /* brand */
  .brand{display:flex;align-items:center;gap:6px;font-family:"Cabin",sans-serif;font-weight:400;color:var(--blue);white-space:nowrap}
  .brand__dot{border-radius:50%;background:var(--orange);flex:none}

  /* front page */
  .front-brand{left:20px;top:14px;width:212px;flex-direction:column;gap:6px;font-size:21px}
  .front-brand .brand__dot{width:40px;height:40px}
  .front-tagline{left:14px;top:90px;width:224px;text-align:center;font-size:6.6px;font-style:italic;font-weight:600;color:var(--ink)}
  .title-band{left:0;top:106px;width:300px;height:155px;background:var(--blue)}
  .course-title{left:18px;top:114px;font-family:"Oswald",sans-serif;color:var(--white);line-height:.95;text-transform:uppercase}
  .course-title span{display:block}
  .course-title .l1{font-size:54px;font-weight:500}
  .course-title .l2{font-size:33px;font-weight:400;letter-spacing:.2px}
  .course-title .l3{font-size:54px;font-weight:500}
  .hero-sky{left:374px;top:18px;width:152px;height:152px;border-radius:50%;background:radial-gradient(circle at 45% 45%,#f6a063,#e97a2c 70%)}
  .hero-main{left:236px;top:30px;width:270px;height:270px;border-radius:50%;background:linear-gradient(135deg,#9fcfe6 0%,#8fbf6a 55%,#6f9a2e 100%)}
  .session-head{left:19px;top:275px;font-family:"Oswald",sans-serif;font-size:20px;line-height:22px;color:var(--orange);font-weight:400}
  .session-when{left:19px;top:299px;font-size:12.4px;font-weight:700;line-height:15px;color:var(--ink)}
  .session-venue{left:19px;top:333px;font-size:12.4px;line-height:15px;font-weight:600;color:var(--ink)}
  .session-venue b{color:var(--orange);font-weight:600}
  .body-copy{font-size:8.6px;line-height:11.2px;color:var(--ink-soft)}
  .session-purpose{left:19px;top:355px;width:478px}
  .who-head{left:19px;top:389px;font-size:15px;line-height:18px;font-weight:700;color:var(--orange)}
  .who-copy{left:19px;top:411px;width:478px;text-align:justify}
  .facilitator-zone{left:0;top:462px;width:512px;height:216px;background:linear-gradient(180deg,var(--paper-grey),#f7f7f7 60%,var(--white))}
  .torn-edge{left:0;top:452px;width:512px;height:18px}
  .portrait{left:19px;top:497px;width:148px;height:148px;border-radius:50%;background:radial-gradient(circle at 50% 45%,#b59a8c,#8a8079 60%,#6a6e75);border:3px solid var(--white)}
  .fac-label{left:182px;top:479px;font-size:11.5px;line-height:14px;font-weight:600;color:var(--ink)}
  .fac-name{left:181px;top:495px;font-family:"Oswald",sans-serif;font-size:21px;line-height:26px;color:var(--orange);font-weight:500}
  .fac-role{left:182px;top:520px;font-size:8.8px;line-height:11px;font-style:italic;font-weight:600;color:var(--ink)}
  .fac-bio{left:182px;top:539px;width:314px;font-size:7.2px;line-height:9.6px;text-align:justify;color:var(--ink-soft)}
  .fac-more{left:182px;top:650px;font-size:10.4px;line-height:13px;color:var(--ink)}
  .fac-more a{color:var(--blue);font-weight:700;text-decoration:none}
  .front-bar{left:0;top:678px;width:512px;height:35px;display:flex}
  .front-bar__phone{width:190px;background:var(--blue);display:flex;align-items:center;gap:9px;padding-left:12px;color:var(--white)}
  .front-bar__phone small{display:block;font-size:6.6px;font-weight:700;letter-spacing:.3px}
  .front-bar__phone strong{display:block;font-family:"Montserrat",sans-serif;font-size:14.5px;line-height:15px}
  .front-bar__info{flex:1;background:var(--green);display:flex;align-items:center;gap:6px;padding-left:16px;font-size:7.6px;font-weight:600;color:var(--ink)}
  .icon-disc{width:22px;height:22px;border-radius:50%;background:var(--black);display:flex;align-items:center;justify-content:center;flex:none}
  .strip{left:0;top:713px;width:512px;height:11px;background:var(--black);color:#bbb;font-size:5.6px;letter-spacing:4.2px;padding-left:14px;line-height:11px}

  /* back page */
  .back-top{left:0;top:0;width:512px;height:74px;background:linear-gradient(180deg,#f1f1f1,#fafafa)}
  .back-brand{left:188px;top:18px;font-size:21px;line-height:20px}
  .back-brand .brand__dot{width:40px;height:40px}
  .what-band{left:0;top:74px;width:512px;height:100px;background:var(--blue-deep)}
  .what-pointer{left:242px;top:172px;width:0;height:0;border-left:16px solid transparent;border-right:16px solid transparent;border-top:16px solid var(--blue-deep)}
  .what-title{left:0;top:82px;width:512px;text-align:center;font-family:"Montserrat",sans-serif;font-weight:800;font-size:28px;color:var(--white)}
  .what-copy{left:22px;top:121px;width:470px;font-size:8.7px;line-height:12px;font-style:italic;color:var(--white);text-align:justify}
  .program-zone{left:0;top:174px;width:512px;height:206px;background:var(--mist)}
  .section-head{font-size:15.5px;line-height:18px;font-weight:700}
  .program-head{left:22px;top:198px;color:var(--blue-deep)}
  .program-copy{left:22px;top:230px;width:198px;text-align:justify}
  .program-copy p+p{margin-top:11px}
  .cycle{left:240px;top:170px;width:272px;height:215px}
  .cycle text{font-family:"Cabin",sans-serif}
  .why-head{left:22px;top:394px;color:var(--orange)}
  .why-copy{left:22px;top:415px;width:218px;text-align:justify}
  .how-head{left:262px;top:394px;color:var(--orange)}
  .how-copy{left:262px;top:415px;width:230px}
  .num-list{list-style:none;margin-top:11px}
  .num-list li{position:relative;padding-left:16px}
  .num-list li::before{content:attr(data-n);position:absolute;left:0;top:1px;width:9px;height:9px;border-radius:50%;color:var(--white);font-size:6.5px;line-height:9px;text-align:center;font-weight:700}
  .num-list--orange li::before{background:var(--orange)}
  .num-list--green li::before{background:var(--green)}
  .how-format{margin-top:7px}
  .path-photo{left:0;top:582px;width:512px;height:96px;background:linear-gradient(180deg,#3a3526 0%,#4d4a32 50%,#2d2b22 100%)}
  .path-edge{left:0;top:574px;width:512px;height:14px}
  .quote{left:0;top:634px;width:512px;text-align:center;font-family:"Dancing Script",cursive;font-size:29px;line-height:36px;color:var(--white)}
  .back-bar{left:0;top:677px;width:512px;height:36px;background:var(--blue);display:flex;align-items:center;justify-content:center;gap:12px;font-family:"Montserrat",sans-serif;font-weight:700;font-size:10.6px;color:var(--black)}
  .back-bar .divider{width:1px;height:22px;background:var(--black)}
  .back-bar__item{display:flex;align-items:center;gap:7px}
</style>
</head>
<body>

<!-- FRONT PAGE -->
<section class="page page--front" aria-label="Front page">
  <div class="abs hero-sky" role="img" aria-label="Photo of sunset clouds in a round crop"></div>
  <div class="abs title-band"></div>
  <div class="abs hero-main" role="img" aria-label="Nature photo of sky and green hills in a round crop"></div>

  <div class="abs brand front-brand"><span class="brand__dot"></span><span>bright meadow</span></div>
  <p class="abs front-tagline">Stillness, Craft and Venture for Bright Meadow</p>

  <h1 class="abs course-title"><span class="l1">Quiet</span><span class="l2">Pathfinder</span><span class="l3">Course</span></h1>

  <h2 class="abs session-head">INFORMATION SESSION</h2>
  <p class="abs session-when">Thursday 5th September 2019,<br>from 19:30 to 21:30</p>
  <p class="abs session-venue"><b>Venue:</b> Lantern Coworking, C/ Almendro 42, Valverde</p>
  <p class="abs body-copy session-purpose">The purpose of this Information Session is to give you a real insight into the Quiet Pathfinder Course and how it can help you get the most out of your work and life.</p>

  <h2 class="abs who-head">Who can come</h2>
  <p class="abs body-copy who-copy">The Information Session is free and whether you come on your own, or with friends or family, you’ll be warmly welcome. It will take place on Thursday the 23rd July 2019, from 19:30 to 21:00, at Lantern Coworking. Please get in touch for more info or to book a place.</p>

  <div class="abs facilitator-zone"></div>
  <svg class="abs torn-edge" viewBox="0 0 512 18" preserveAspectRatio="none" aria-hidden="true">
    <path d="M0 10 L18 8 L34 12 L52 7 L70 11 L92 6 L110 10 L130 8 L150 12 L172 7 L194 11 L216 8 L238 12 L260 7 L282 10 L304 8 L326 12 L348 7 L370 11 L392 8 L414 12 L436 7 L458 10 L480 8 L500 11 L512 9 L512 18 L0 18 Z" fill="var(--paper-grey)"/>
  </svg>
  <div class="abs portrait" role="img" aria-label="Portrait photo of the facilitator in a round crop"></div>
  <p class="abs fac-label">Facilitator</p>
  <h2 class="abs fac-name">DR TOMAS VARELA</h2>
  <p class="abs fac-role">Visiting Research Fellow, University of Northmere</p>
  <p class="abs fac-bio">Tomas joined the University of Northmere (School of Management) as a Lecturer in Entrepreneurship in 2015. He completed his PhD in Entrepreneurship at Eastbrook Business School in 2014. His work received the Lindqvist Doctoral Dissertation Award from the Society for Management Studies. He began his business career as a production engineer (Voltrix), and continued in sales (Kernwerk). After his MBA, he worked as a strategy consultant at Riverside Business School. Originally from Portugal, Tomas enjoys designing and launching new ideas, international communities, mindfulness retreats, and musical improvisation. He nurtures a close connection to Stillwater Mindfulness Centre, where he has practiced and volunteered over 9 months. He has a broad experience of sharing the benefits of mindfulness with others.</p>
  <p class="abs fac-more">More about the facilitator: <a>www.profilehub.com/in/tvarela</a></p>

  <div class="abs front-bar">
    <div class="front-bar__phone">
      <span class="icon-disc"><svg width="12" height="12" viewBox="0 0 24 24"><path d="M6.6 10.8a15.1 15.1 0 0 0 6.6 6.6l2.2-2.2a1 1 0 0 1 1-.25 11.4 11.4 0 0 0 3.6.57 1 1 0 0 1 1 1V20a1 1 0 0 1-1 1A17 17 0 0 1 3 4a1 1 0 0 1 1-1h3.5a1 1 0 0 1 1 1 11.4 11.4 0 0 0 .57 3.6 1 1 0 0 1-.25 1z" fill="#fff"/></svg></span>
      <span><small>INFORMATION &amp; BOOKING:</small><strong>+34 611 402 735</strong></span>
    </div>
    <div class="front-bar__info">
      <svg width="9" height="11" viewBox="0 0 24 30"><path d="M12 0a10 10 0 0 0-10 10c0 7.5 10 20 10 20s10-12.5 10-20A10 10 0 0 0 12 0zm0 14a4 4 0 1 1 0-8 4 4 0 0 1 0 8z" fill="var(--black)"/></svg>
      <span>Lantern Coworking, C/ Almendro 42, Valverde</span>
      <svg style="margin-left:6px" width="11" height="11" viewBox="0 0 24 24"><circle cx="12" cy="12" r="12" fill="var(--black)"/><path d="M6 8h12v8H6z M6 8l6 5 6-5" fill="none" stroke="#fff" stroke-width="1.6"/></svg>
      <span>info@brightmeadow.io</span>
    </div>
  </div>
  <p class="abs strip">VIDEO CALL AND MESSAGING</p>
</section>

<!-- BACK PAGE -->
<section class="page page--back" aria-label="Back page">
  <div class="abs back-top"></div>
  <div class="abs brand back-brand"><span class="brand__dot"></span><span>bright<br>meadow</span></div>

  <div class="abs what-band"></div>
  <div class="abs what-pointer"></div>
  <h1 class="abs what-title">What is Quiet Pathfinding</h1>
  <p class="abs what-copy">Being mindful means being aware and awake. Entrepreneurship is the creation of a new form of organising. Quiet Pathfinding is then the process of creating or redesigning your work and life with awareness, in a way that is reflective of you, of your passions and values, thus conducing to a greater sense of fulfilment and happiness.</p>

  <div class="abs program-zone"></div>
  <h2 class="abs section-head program-head">The Program</h2>
  <div class="abs body-copy program-copy">
    <p><b>The Quiet Pathfinder Course</b> is a <b>4-month long transformative journey</b> designed for people who feel stuck or not entirely satisfied with their work and/or life. It is of benefit for everyone, at any stage.</p>
    <p>The Program consists of a 5-hour workshop each month, with 2-hour weekly peer support meetings. It combines mindfulness techniques, design thinking methodology, and entrepreneurship frameworks.</p>
  </div>

  <svg class="abs cycle" viewBox="0 0 272 215" role="img" aria-label="Cycle of four workshops: Insight, Design, Execute, Present, joined by weekly peer support meetings">
    <defs>
      <marker id="arrowhead" viewBox="0 0 10 10" refX="5" refY="5" markerWidth="4" markerHeight="4" orient="auto"><path d="M0 0L10 5L0 10z" fill="context-stroke"/></marker>
    </defs>
    <g fill="none" stroke-width="5" stroke-linecap="round">
      <path d="M162 48 Q178 52 184 66" stroke="var(--green)" marker-end="url(#arrowhead)"/>
      <path d="M190 132 Q184 148 170 152" stroke="var(--blue)" marker-end="url(#arrowhead)"/>
      <path d="M106 152 Q92 148 86 134" stroke="var(--orange)" marker-end="url(#arrowhead)"/>
      <path d="M82 70 Q88 54 104 50" stroke="#9a9a9a" marker-end="url(#arrowhead)"/>
    </g>
    <g font-weight="700" text-anchor="middle" fill="#fff">
      <circle cx="123" cy="44" r="38" fill="var(--green)" stroke="#fff" stroke-width="3"/>
      <text x="123" y="37" font-size="7">Workshop 1</text><text x="123" y="50" font-size="11.5">INSIGHT</text><text x="123" y="60" font-size="7" font-style="italic">(5 hours)</text>
      <circle cx="190" cy="104" r="38" fill="var(--blue)" stroke="#fff" stroke-width="3"/>
      <text x="190" y="97" font-size="7">Workshop 2</text><text x="190" y="110" font-size="11.5">DESIGN</text><text x="190" y="120" font-size="7" font-style="italic">(5 hours)</text>
      <circle cx="122" cy="162" r="38" fill="var(--orange)" stroke="#fff" stroke-width="3"/>
      <text x="122" y="155" font-size="7">Workshop 3</text><text x="122" y="168" font-size="11.5">EXECUTE</text><text x="122" y="178" font-size="7" font-style="italic">(5 hours)</text>
      <circle cx="58" cy="104" r="38" fill="#a9a9a9" stroke="#fff" stroke-width="3"/>
      <text x="58" y="97" font-size="7">Workshop 4</text><text x="58" y="110" font-size="11.5">PRESENT</text><text x="58" y="120" font-size="7" font-style="italic">(5 hours)</text>
    </g>
    <g font-size="6.6" font-weight="700" fill="var(--ink)" text-anchor="middle">
      <text x="32" y="42">WPS meetings</text>
      <text x="232" y="42">Weekly Peer Support</text>
      <text x="232" y="51">(WPS) meetings</text>
      <text x="232" y="60">(2 hours)</text>
      <text x="27" y="168">WPS meetings</text>
      <text x="228" y="168">WPS meetings</text>
    </g>
  </svg>

  <h2 class="abs section-head why-head">Why</h2>
  <div class="abs body-copy why-copy">
    <p>Many people are not satisfied with their work, but they don’t know what to do about it. This Program offers you a safe place to conduct your inner journey with collective support, helping you reflect, design, and (very likely) do something about it. It aims at:</p>
    <ol class="num-list num-list--orange">
      <li data-n="1">Increasing awareness, clarity and confidence</li>
      <li data-n="2">Having a deeper <b><i>insight</i></b> on what makes you happier and what you want</li>
      <li data-n="3">Developing a clear <b><i>design</i></b> integrating your intended work and life</li>
      <li data-n="4">Start <i>executing</i> this design</li>
    </ol>
  </div>

  <h2 class="abs section-head how-head">How</h2>
  <div class="abs body-copy how-copy">
    <p>This Program differs from existing entrepreneurial programs in many ways:</p>
    <ol class="num-list num-list--green">
      <li data-n="1">Uses mindfulness and self analysis to look deeply into yourself</li>
      <li data-n="2">Design and execution decisions are based on happiness rather than (only) financials</li>
      <li data-n="3">Holistic and inclusive design process, integrating work and life, and building synergies between your different parts</li>
    </ol>
    <p class="how-format">Format includes: lectures, individual work, group sharing, guided activities, experiential exercises, video, audio, handouts and other resources.</p>
  </div>

  <div class="abs path-photo" role="img" aria-label="Photo of a person walking along a forest path between tall trees"></div>
  <svg class="abs path-edge" viewBox="0 0 512 14" preserveAspectRatio="none" aria-hidden="true">
    <path d="M0 14 L0 8 L20 10 L40 6 L62 9 L84 5 L106 9 L128 7 L150 10 L172 6 L196 9 L220 5 L244 9 L268 7 L292 10 L316 6 L340 9 L364 5 L388 9 L412 7 L436 10 L460 6 L486 9 L512 6 L512 14 Z" fill="#3a3526"/>
  </svg>
  <p class="abs quote">“The way out is in”</p>

  <div class="abs back-bar">
    <span class="back-bar__item">
      <span class="icon-disc"><svg width="12" height="12" viewBox="0 0 24 24"><path d="M6.6 10.8a15.1 15.1 0 0 0 6.6 6.6l2.2-2.2a1 1 0 0 1 1-.25 11.4 11.4 0 0 0 3.6.57 1 1 0 0 1 1 1V20a1 1 0 0 1-1 1A17 17 0 0 1 3 4a1 1 0 0 1 1-1h3.5a1 1 0 0 1 1 1 11.4 11.4 0 0 0 .57 3.6 1 1 0 0 1-.25 1z" fill="#fff"/></svg></span>
      +34 611 402 735 (video call and messaging)
    </span>
    <span class="divider"></span>
    <span class="back-bar__item">
      <span class="icon-disc"><svg width="12" height="12" viewBox="0 0 24 24"><path d="M3 6h18v12H3z M3 6l9 7 9-7" fill="none" stroke="#fff" stroke-width="2"/></svg></span>
      info@brightmeadow.io
    </span>
  </div>
  <div class="abs strip"></div>
</section>

</body>
</html>
```